RTavenor Business Cards & Letterhead

I have a logo but need a design for some new business cards. We are a Design-Build Firm that specializes in the design and construction of commercial projects.
the cards need to be professional. no cartoon stuff.
i would like to have the cards in AI format so I can update the card as needed. Logo is provided.
Our Address is: 4187 Marlowe Ct. Cedar Glen, Ohio 27614

```html
<!DOCTYPE html>
<html lang="en">
<head>
<meta charset="utf-8">
<title>RTavenor Business Card</title>
<link rel="stylesheet" href="https://fonts.googleapis.com/css2?family=Open+Sans:wght@400;600;700&display=swap">
<style>
  :root {
    --stage: #333333;
    --paper: #ffffff;
    --ink: #1b1b1b;
    --logo-grey: #606165;
    --brand-blue: #1a6fae;
    --band-light: #1a82c6;
    --band-dark: #0d4775;
    --rule: #3a3a3a;
  }
  * { box-sizing: border-box; margin: 0; padding: 0; }
  html, body {
    width: 1200px; height: 780px; overflow: hidden;
    background: var(--stage);
    font-family: "Open Sans", Arial, sans-serif;
  }
  .sheet {
    width: 1200px; height: 780px;
    display: flex; align-items: center; justify-content: center; gap: 40px;
  }
  .card {
    position: relative;
    width: 560px; height: 320px;
    background: var(--paper);
    box-shadow: 0 10px 30px rgba(0,0,0,.45);
    overflow: hidden;
  }
  .wordmark {
    display: flex; align-items: center; gap: 10px;
    color: var(--logo-grey);
    font-weight: 700; letter-spacing: 1px;
    text-transform: uppercase; line-height: 1;
  }
  .wordmark__square { background: var(--brand-blue); flex: none; }

  /* back */
  .card--back { display: flex; align-items: center; justify-content: center; }
  .card--back .wordmark { font-size: 62px; }
  .card--back .wordmark__square { width: 46px; height: 46px; }

  /* front */
  .card--front .wordmark {
    position: absolute; top: 52px; left: 0; right: 0;
    justify-content: center; font-size: 50px;
  }
  .card--front .wordmark__square { width: 38px; height: 38px; }

  .person {
    position: absolute; left: 36px; top: 160px; width: 250px; text-align: right;
  }
  .person__name {
    color: var(--brand-blue); font-weight: 700; font-size: 25px; letter-spacing: .5px;
  }
  .person__title { color: var(--ink); font-weight: 600; font-size: 16px; margin-top: -2px; }

  .divider {
    position: absolute; left: 300px; top: 148px; width: 1px; height: 92px; background: var(--rule);
  }
  .contacts {
    position: absolute; left: 318px; top: 150px; list-style: none;
    font-size: 15px; color: var(--ink);
  }
  .contacts li { display: flex; align-items: center; gap: 9px; height: 26px; }
  .contacts svg { width: 15px; height: 15px; flex: none; }

  .address-band {
    position: absolute; left: 0; right: 0; top: 248px; height: 30px;
    background: linear-gradient(90deg, var(--band-light), var(--band-dark));
    color: var(--paper); font-size: 15px; font-weight: 600; letter-spacing: .3px;
    display: flex; align-items: center; justify-content: center;
  }
</style>
</head>
<body>
<main class="sheet">
  <section class="card card--back" aria-label="Card back">
    <div class="wordmark"><span class="wordmark__square"></span><span>RTavenor</span></div>
  </section>

  <section class="card card--front" aria-label="Card front">
    <div class="wordmark"><span class="wordmark__square"></span><span>RTavenor</span></div>

    <div class="person">
      <p class="person__name">MILES TAVENOR</p>
      <p class="person__title">Founder/President</p>
    </div>

    <div class="divider"></div>

    <ul class="contacts">
      <li>
        <svg viewBox="0 0 24 24" aria-hidden="true"><path fill="var(--brand-blue)" d="M6.6 10.8a15.1 15.1 0 0 0 6.6 6.6l2.2-2.2c.3-.3.7-.4 1-.2 1.1.4 2.3.6 3.6.6.6 0 1 .4 1 1V20c0 .6-.4 1-1 1C10.6 21 3 13.4 3 4c0-.6.4-1 1-1h3.5c.6 0 1 .4 1 1 0 1.3.2 2.5.6 3.6.1.3 0 .7-.2 1z"/></svg>
        <span>(555) 302-0148</span>
      </li>
      <li>
        <svg viewBox="0 0 24 24" aria-hidden="true"><circle cx="12" cy="12" r="9" fill="none" stroke="var(--brand-blue)" stroke-width="2"/><path d="M3 12h18M12 3c3 3 3 15 0 18M12 3c-3 3-3 15 0 18" fill="none" stroke="var(--brand-blue)" stroke-width="1.6"/></svg>
        <span>www.rtavenor.com</span>
      </li>
      <li>
        <svg viewBox="0 0 24 24" aria-hidden="true"><rect x="2" y="5" width="20" height="14" rx="1.5" fill="none" stroke="var(--brand-blue)" stroke-width="2"/><path d="M3 6l9 7 9-7" fill="none" stroke="var(--brand-blue)" stroke-width="2"/></svg>
        <span>MST@RTavenor.com</span>
      </li>
    </ul>

    <div class="address-band">4187 Marlowe Ct. Cedar Glen, Ohio 27614</div>
  </section>
</main>
</body>
</html>
```